Brisk Hollow toothpaste tube design

Design a Brisk Hollow tube design for our all natural toothpaste. The toothpaste is 100% natural with a smooth marshmallow consistency. It's unique because it's not pastelike at all. The all natural flavors make the toothpaste taste great. The toothpaste is smooth yet still leaves your mouth feeling squeaky clean. We want to market this as an all natural family toothpaste.

The flavor is Mint. (possibly called "Breezy Mint")

We have included our logo (eps & jpg), information that goes on the back of the tube, and the artwork template from the tube supplier for the 4.2oz tube.

We like a vintage earthy retro look and feel but we are not limited to this.

The tubes stand upright as shown in the picture of File 4.
Updates

The finished artwork must include anĀ adobe illustratorĀ file.

I would like to thank all of the designers for their work on this project. We had a difficult time making a decision since all of the designs were very close to what we expected.

Sincerely,

Glen

Target Market(s)

The target market is families that desire an all natural toothpaste. We will be stressing the 100% natural and great taste.

Requirements
Must have
• Three colors maximum due to tube manufacture restrictions.

Must have "100% natural" and "fluoride free" on front of tube. A reference to the great taste or flavor is also important.

Must say 4.2 oz on the front of the tube, centered, at the bottom.
Nice to have
• Fun, colorful packaging that will stand out. Go to your local store and stand in front of the tootpaste shelves, give us something different!
Should not have
• We do not want a lot of red or blue because these are predominate colors already in use on toothpaste tubes and boxes.

```html
<!DOCTYPE html>
<html lang="en">
<head>
<meta charset="utf-8">
<title>Brisk Hollow Toothpaste Tube</title>
<link href="https://fonts.googleapis.com/css2?family=Open+Sans:wght@400;600;700;800&family=Roboto+Condensed:wght@400;700&family=Courgette&display=swap" rel="stylesheet">
<style>
  :root {
    --leaf-green: #2f8a3c;
    --deep-green: #2a7432;
    --soft-green: #a9d2a1;
    --tube-white: #ffffff;
    --tube-edge: #e3e6e3;
    --page: #ffffff;
    --ink: #3d8f44;
    --weight-ink: #333333;
  }
  * { margin: 0; padding: 0; box-sizing: border-box; }
  html, body { width: 1200px; height: 898px; overflow: hidden; background: var(--page); }
  body { position: relative; font-family: "Open Sans", Arial, sans-serif; }

  .tube { position: absolute; top: 60px; width: 306px; height: 775px; }
  .tube--front { left: 290px; }
  .tube--back { left: 622px; }

  .tube__crimp {
    position: absolute; top: 0; left: 0; right: 0; height: 30px;
    background: var(--tube-white); border: 1px solid var(--tube-edge);
    border-radius: 3px;
  }
  .tube__body {
    position: absolute; top: 30px; left: 0; right: 0; height: 690px;
    background: var(--tube-white); border: 1px solid var(--tube-edge);
    border-radius: 2px 2px 8px 8px; overflow: hidden;
  }
  .tube__cap {
    position: absolute; top: 722px; left: 10px; right: 10px; height: 52px;
    background: var(--tube-white); border: 1px solid var(--tube-edge);
    border-radius: 4px 4px 10px 10px;
  }

  .brand { position: absolute; left: 0; right: 0; text-align: center; color: var(--leaf-green); }
  .brand__row { display: flex; align-items: center; justify-content: center; gap: 8px; }
  .brand__name { font-weight: 800; line-height: 1; }
  .brand__dot { border-radius: 50%; background: var(--leaf-green); flex: none; }
  .brand__tagline { font-weight: 700; letter-spacing: 1px; text-transform: uppercase; }

  .tube--front .brand { top: 52px; }
  .tube--front .brand__name { font-size: 50px; }
  .tube--front .brand__dot { width: 16px; height: 16px; }
  .tube--front .brand__tagline { font-size: 12px; margin-top: 10px; }

  .claim-band {
    position: absolute; top: 252px; left: 30px; right: 30px; height: 76px;
    background: var(--soft-green); color: #fff;
    font-weight: 700; font-size: 14.5px; line-height: 1.15; text-align: center;
    padding: 4px 10px 0;
  }
  .flavor-panel {
    position: absolute; top: 328px; left: 30px; right: 30px; height: 272px;
    background: var(--deep-green);
  }
  .flavor-panel__name {
    position: absolute; top: 6px; left: 0; right: 0; text-align: center;
    font-family: "Courgette", cursive; color: #fff; font-size: 28px; line-height: 40px;
  }
  .flavor-panel__leaves {
    position: absolute; top: 52px; left: 0; right: 0; bottom: 0;
    background: linear-gradient(160deg, #3c8d42 0%, #236a2c 60%, #1f5f28 100%);
  }
  .net-weight {
    position: absolute; top: 640px; left: 0; right: 0; text-align: center;
    font-weight: 700; font-size: 20px; line-height: 26px; color: var(--weight-ink);
  }

  .seal { position: absolute; left: -62px; top: 432px; width: 136px; height: 136px; }

  .tube--back .brand { top: 45px; }
  .tube--back .brand__name { font-size: 30px; }
  .tube--back .brand__dot { width: 10px; height: 10px; }
  .tube--back .brand__tagline { font-size: 8px; margin-top: 6px; }

  .back-copy {
    position: absolute; top: 147px; left: 36px; right: 36px;
    color: var(--ink); font-family: "Roboto Condensed", "Arial Narrow", sans-serif;
    font-size: 12.5px; line-height: 17px; text-align: center;
  }
  .back-copy p + p { margin-top: 17px; }
</style>
</head>
<body>

  <section class="tube tube--front" aria-label="Front of tube">
    <div class="tube__crimp"></div>
    <div class="tube__body">
      <div class="brand">
        <div class="brand__row">
          <span class="brand__name">Brisk<br>Hollow</span>
          <span class="brand__dot"></span>
        </div>
        <div class="brand__tagline">Make every day a brisk day</div>
      </div>
      <div class="claim-band">An all natural flavoured toothpaste for the whole family with a smooth, great taste.</div>
      <div class="flavor-panel">
        <div class="flavor-panel__name">breezy mint</div>
        <div class="flavor-panel__leaves" role="img" aria-label="Illustration of mint leaves"></div>
      </div>
      <div class="net-weight">4.2oz</div>
    </div>
    <div class="tube__cap"></div>
    <svg class="seal" viewBox="0 0 136 136" role="img" aria-label="100% natural, fluoride free seal">
      <defs>
        <path id="seal-top" d="M22,68 A46,46 0 0 1 114,68"/>
        <path id="seal-bottom" d="M14,68 A54,54 0 0 0 122,68"/>
      </defs>
      <circle cx="68" cy="68" r="66" fill="#ffffff" fill-opacity="0.85"/>
      <circle cx="68" cy="68" r="64" fill="none" stroke="var(--leaf-green)" stroke-width="3"/>
      <circle cx="68" cy="68" r="32" fill="none" stroke="var(--leaf-green)" stroke-width="2"/>
      <text fill="var(--leaf-green)" font-family="Open Sans, sans-serif" font-weight="700" font-size="13" letter-spacing="1">
        <textPath href="#seal-top" startOffset="50%" text-anchor="middle">100% NATURAL</textPath>
      </text>
      <text fill="var(--leaf-green)" font-family="Open Sans, sans-serif" font-weight="700" font-size="12" letter-spacing="1">
        <textPath href="#seal-bottom" startOffset="50%" text-anchor="middle" dominant-baseline="hanging">FLUORIDE FREE</textPath>
      </text>
    </svg>
  </section>

  <section class="tube tube--back" aria-label="Back of tube">
    <div class="tube__crimp"></div>
    <div class="tube__body">
      <div class="brand">
        <div class="brand__row">
          <span class="brand__name">Brisk Hollow</span>
          <span class="brand__dot"></span>
        </div>
        <div class="brand__tagline">Make every day a brisk day</div>
      </div>
      <div class="back-copy">
        <p>Directions:<br>Adults and children 2 years of age and older: Brush teeth thoroughly, preferably after each meal or at least twice a day or as directed by a dentist. Children under 2: consult a dentist.</p>
        <p>Natural Ingredients: vegetable glycerin, de-ionized water, xylitol, calcium carbonate, USDA organic flavor concentrate, sodium coco-sulfate (derived from coconut oil), and carrageenan (extracted from seaweed).</p>
        <p>No parabens, no gluten, no glycols, no SLS, no TEA, no formaldehyde, no artificial flavors, no artificial dye, no artificial sweetener, no dairy, no sorbitol, no saccharines, no peroxides, and no fluoride!</p>
        <p>Made in USA<br>Distribution &amp; Supply Facility:<br>Brisk Hollow LLC<br>4120 Alder Ln<br>Fernvale, MI 48020<br>www.briskhollow.com<br>info@briskhollow.com</p>
      </div>
    </div>
    <div class="tube__cap"></div>
  </section>

</body>
</html>
```